This book will apply the 12 Steps to gaming addiction, also known as video game addiction. The primary purpose of the book is to provide an effective solution for this new type of addiction. The solution is based on the rich and successful concepts of traditional twelve-step programs like RQ.

The title on the cover will be "Nine Doors Out of the Endless Level" and "by Peter Halvorn". A subtitle can be used if it works in your design of "A Practical Path Back from Compulsive Screen Play". Cover will be for a 6" x 9" book approximately 110 pages in length.

Some back cover text including some review quotes and an author bio are in the attached Word doc. There is also an author photo attached for for the back cover.

Requirements
Must have
• For the cover design it could be stylized, or an image, a partial image, or whatever. I am open to suggestions. Think about what would be noticed by a person searching for help with moderating their video game use, or by the parents or loved ones of problem gamers. Something contemporary and eye catching.

```html
<!DOCTYPE html>
<html lang="en">
<head>
<meta charset="utf-8">
<title>Nine Doors Out of the Endless Level — Book Cover</title>
<link rel="stylesheet" href="https://fonts.googleapis.com/css2?family=Poppins:wght@400;600;700;800;900&display=swap">
<style>
  :root {
    --page-bg: #e4e4e4;
    --cover-bg: #ffffff;
    --ink: #1c1c1e;
    --blue-light: #1fa6dc;
    --blue-deep: #0b6d9f;
    --blob: #c4e2f3;
    --ring: #4a8fd4;
    --art-teal: #6fd9e2;
    --art-pink: #f2a9d3;
    --art-violet: #7a5cc4;
    --rule: #2a2a2a;
  }
  * { box-sizing: border-box; margin: 0; padding: 0; }
  html, body {
    width: 1200px;
    height: 800px;
    overflow: hidden;
    background: var(--page-bg);
  }
  body {
    display: flex;
    align-items: center;
    justify-content: center;
    font-family: "Poppins", sans-serif;
  }
  .cover {
    position: relative;
    width: 508px;
    height: 762px;
    background: var(--cover-bg);
    overflow: hidden;
    box-shadow: 0 6px 24px rgba(0,0,0,0.12);
  }
  .cover-decor {
    position: absolute;
    inset: 0;
    width: 100%;
    height: 100%;
  }
  .title-block {
    position: absolute;
    top: 46px;
    left: 0;
    right: 0;
    text-align: center;
    line-height: 1;
  }
  .title-lead {
    font-weight: 800;
    font-size: 30px;
    letter-spacing: -0.5px;
    color: var(--ink);
  }
  .title-accent {
    display: inline-block;
    margin-top: 6px;
    font-weight: 900;
    font-size: 96px;
    letter-spacing: -3px;
    background: linear-gradient(180deg, var(--blue-light) 0%, var(--blue-deep) 100%);
    -webkit-background-clip: text;
    background-clip: text;
    color: transparent;
  }
  .title-close {
    margin-top: 2px;
    font-weight: 900;
    font-size: 86px;
    letter-spacing: -2px;
    color: var(--ink);
  }
  .title-rule {
    position: absolute;
    top: 308px;
    left: 56px;
    right: 56px;
    height: 2px;
    background: linear-gradient(90deg, transparent, var(--rule) 15%, var(--rule) 85%, transparent);
  }
  .subtitle {
    position: absolute;
    top: 322px;
    left: 0;
    right: 0;
    text-align: center;
    font-weight: 700;
    font-size: 22px;
    line-height: 1.3;
    color: var(--ink);
  }
  .cover-art {
    position: absolute;
    top: 412px;
    left: 92px;
    width: 330px;
    height: 262px;
    border-radius: 46% 54% 48% 52% / 55% 48% 52% 45%;
    background: linear-gradient(115deg, var(--art-teal) 0%, #9fd6ee 40%, var(--art-pink) 78%, var(--art-violet) 100%);
  }
  .byline {
    position: absolute;
    bottom: 30px;
    left: 0;
    right: 0;
    text-align: center;
    font-size: 22px;
    color: var(--ink);
  }
  .byline-name { font-weight: 700; }
</style>
</head>
<body>
  <main class="cover">
    <svg class="cover-decor" viewBox="0 0 508 762" aria-hidden="true">
      <path class="blob-corner" d="M390 0 H508 V70 C470 60 430 40 390 0 Z" fill="var(--blob)"/>
      <path class="blob-left" d="M0 40 C30 90 22 150 12 200 C4 240 0 270 0 300 Z" fill="var(--blob)"/>
      <path class="blob-right" d="M508 338 C470 360 440 390 438 425 C436 460 470 475 485 500 C498 520 504 540 508 560 Z" fill="var(--blob)"/>
      <circle class="ring-top" cx="36" cy="28" r="13" fill="none" stroke="var(--ring)" stroke-width="2.5"/>
      <circle class="ring-bottom" cx="452" cy="700" r="13" fill="none" stroke="var(--ring)" stroke-width="2.5"/>
    </svg>

    <header class="title-block">
      <h1>
        <div class="title-lead">NINE DOORS OUT OF THE</div>
        <div class="title-accent">ENDLESS</div>
        <div class="title-close">LEVEL</div>
      </h1>
    </header>

    <div class="title-rule"></div>

    <p class="subtitle">A Practical Path Back from<br>Compulsive Screen Play</p>

    <div class="cover-art" role="img" aria-label="Illustration of a young person in headphones, seen from behind, holding a game controller in front of a monitor showing a shooter game, on a teal and pink backdrop"></div>

    <p class="byline">by <span class="byline-name">Peter Halvorn</span></p>
  </main>
</body>
</html>
```